Hong Kong based International Remittance and ForEx company requires website design

We need a website designed for a new European - Hong Kong based ForEx & fund remittence entity.

The company specialises in larger corporate & high net worth private client trades, therefore the design must aesthetically reflect this (sophisticated). As a theme colour, financial entities tend to use either blue or red; if blue, our preference is a darker blue. Visually, our preference is less copy, more imagery.

Number of pages would be limited; landing (home), about us, client registration (x1 Corporate form, x1 Private Client form), Contact Us.

Have uploaded the existing logo - please note this is to be redesigned, although the colour scheme will remain the same. Please also note that copy will follow - please use Lorem Ipsum.

Target Market(s)

Medium to large Corporations. High net worth individuals.

Industry/Entity Type

Financial Service

Coding

Coded - Design and coding required

Number of Pages Required

4 page

Font styles to use
Serif

Requirements
Nice to have
• ForEx ticker,

```html
<!DOCTYPE html>
<html lang="en">
<head>
<meta charset="utf-8">
<title>Harbourline Incorporation</title>
<link rel="stylesheet" href="https://fonts.googleapis.com/css2?family=Crimson+Text:wght@400;600&family=Merriweather:wght@400;700&family=Raleway:wght@400;500;600;700&display=swap">
<style>
:root{
  --navy:#0d2b5e;
  --navy-deep:#0a2350;
  --ticker-blue:#3d8fe6;
  --ink:#1e1e1e;
  --text:#555a60;
  --muted:#8a8f95;
  --white:#ffffff;
  --light-bg:#efefef;
  --dark-btn:#3a3a3a;
  --footer-bg:#232323;
  --footer-line:#3a3a3a;
  --field:#3f3f3f;
  --bright-blue:#0b4fb0;
}
*{box-sizing:border-box;margin:0;padding:0}
html,body{width:1200px;height:2497px;overflow:hidden}
body{font-family:"Raleway",sans-serif;color:var(--text);background:var(--white);position:relative}
.serif{font-family:"Crimson Text",serif}
section,header,footer,div{position:relative}
.abs{position:absolute}

/* header */
.site-header{height:133px;border-top:4px solid var(--navy);background:var(--white)}
.brand{position:absolute;left:100px;top:46px;display:flex;align-items:center;gap:12px}
.brand-dot{width:34px;height:34px;border-radius:50%;background:#c9d3de}
.brand-name{font-family:"Merriweather",serif;font-weight:400;font-size:27px;color:var(--ink)}
.main-nav{position:absolute;right:97px;top:52px;display:flex;gap:0;align-items:center}
.main-nav a{font-size:15px;color:var(--ink);text-decoration:none;padding:6px 0;margin-left:48px}
.main-nav a.active{border:1.5px solid #444;border-radius:18px;padding:6px 14px;margin-left:0}

/* ticker */
.ticker{height:42px;background:var(--ticker-blue);display:flex;align-items:center;color:var(--white)}
.ticker-label{width:213px;height:42px;background:var(--navy-deep);display:flex;align-items:center;justify-content:center;font-size:14px;font-weight:700;border-right:4px solid #cfe2f8}
.ticker-items{display:flex;font-size:14px;flex:1}
.ticker-items span{margin-left:28px;margin-right:36px}
.ticker-next{position:absolute;right:14px;top:10px}

/* hero */
.hero{height:474px;background:radial-gradient(ellipse at 72% 55%,#3b5a7d 0%,#1c2a3a 40%,#0e1520 80%);color:var(--white)}
.hero-art{position:absolute;left:560px;top:0;width:640px;height:474px;background:linear-gradient(120deg,rgba(40,80,120,0) 0%,rgba(80,140,190,.35) 55%,rgba(20,40,60,.2) 100%)}
.hero-mark{position:absolute;left:100px;top:70px;width:62px;height:62px;border-radius:50%;background:#9aa4ae}
.hero-title{position:absolute;left:100px;top:155px;font-family:"Merriweather",serif;font-weight:700;font-size:40px}
.hero-text{position:absolute;left:100px;top:226px;font-size:17px;line-height:31px;width:420px}
.btn{display:inline-flex;align-items:center;justify-content:center;height:40px;border-radius:20px;font-size:14px;text-decoration:none}
.btn-outline{position:absolute;left:100px;top:325px;width:120px;border:1.5px solid var(--white);color:var(--white);background:var(--navy)}
.dots{position:absolute;display:flex;gap:12px}
.hero .dots{left:555px;top:394px}
.hero .dots i{width:15px;height:15px;border:2px solid var(--white);border-radius:50%}

/* divider */
.divider{position:absolute;left:570px;width:60px;height:60px;border-radius:50%;background:var(--white);z-index:3}

/* about */
.about{height:363px;text-align:center}
.section-title{font-size:33px;color:var(--ink);display:inline-block;padding-bottom:4px;border-bottom:1.5px solid var(--navy)}
.section-title b{font-weight:400;color:var(--navy)}
.about .section-title{margin-top:18px}
.about .lead{font-size:13px;margin-top:10px;color:var(--text)}
.about .body{width:920px;margin:22px auto 0;font-size:13.5px;line-height:24px}
.about .body p+p{margin-top:10px}
.about .actions{margin-top:28px;display:flex;gap:16px;justify-content:center}
.btn-navy{width:118px;background:var(--navy);color:var(--white)}
.btn-dark{width:118px;background:var(--dark-btn);color:var(--white)}

/* services */
.services{height:544px;background:linear-gradient(180deg,#2b2e35 0%,#24272d 100%);text-align:center;color:var(--white)}
.services .section-title{color:var(--white);margin-top:50px;border-color:#999}
.services .lead{font-size:13px;margin-top:12px;color:#ddd}
.service-card{position:absolute;top:173px;width:288px;height:243px;background:var(--white);border:5px solid var(--white);text-align:left}
.service-photo{height:188px}
.service-card h3{font-size:15px;font-weight:700;color:var(--ink);padding:14px 3px}
.service-card.featured{background:linear-gradient(160deg,#1f4a86,#173a6c);border-color:var(--white);text-align:center}
.featured h3{color:var(--white);font-weight:500;font-size:21px;padding:40px 0 0}
.featured p{font-size:13px;line-height:22px;padding:20px 26px 0;color:#e3eaf4}
.featured .btn{width:104px;height:34px;border:1.5px solid #ddd;color:var(--white);margin-top:16px;font-size:13px}
.services .dots{left:542px;top:465px}
.services .dots i{width:8px;height:8px;border-radius:50%;background:#888}
.services .dots i.on{background:var(--ticker-blue)}

/* blog */
.blog{height:507px;background:var(--light-bg);text-align:center}
.blog .section-title{margin-top:34px;font-size:34px}
.post-card{position:absolute;top:100px;width:300px;height:341px;background:var(--white);border:1px solid #ddd;text-align:left;padding:6px}
.post-photo{height:156px}
.post-card h3{font-size:15px;font-weight:700;color:var(--ink);margin:24px 6px 0}
.post-card p{font-size:12.5px;line-height:20px;margin:8px 6px 0}
.post-card .btn{border-radius:0;width:100px;height:37px;margin:18px 6px 0;font-size:14px}

/* footer */
.site-footer{height:370px;background:var(--footer-bg);color:#ccc}
.footer-col{position:absolute;top:0;height:310px}
.footer-sep{position:absolute;top:55px;width:1px;height:255px;background:var(--footer-line)}
.footer-brand{position:absolute;left:100px;top:60px;display:flex;align-items:center;gap:10px}
.footer-brand .brand-name{color:var(--white);font-size:24px}
.contact-list{position:absolute;left:100px;top:172px;font-size:13.5px;line-height:30px;list-style:none}
.contact-list li{display:flex;gap:16px}
.contact-list svg{margin-top:9px;flex:none}
.footer-title{font-size:20px;color:var(--white);font-weight:500}
.recent{left:384px;top:70px}
.recent-item{display:flex;gap:14px;margin-top:20px}
.recent-item:first-of-type{margin-top:24px}
.recent-thumb{width:52px;height:46px}
.recent-item h4{font-size:12.5px;color:var(--white);font-weight:600;margin-top:4px}
.recent-item time{font-size:11px;display:block;margin-top:12px;color:#bbb}
.links{left:671px;top:70px}
.links ul{list-style:none;margin-top:20px;font-size:13.5px;line-height:31px}
.contact{left:882px;top:70px;width:218px}
.field{height:37px;background:var(--field);border-radius:5px;margin-top:12px;font-size:13px;padding:10px 14px;color:#ddd}
.field:first-of-type{margin-top:24px}
.field.area{height:63px}
.contact .submit{height:37px;background:var(--bright-blue);border-radius:4px;margin-top:13px;display:flex;align-items:center;justify-content:center;color:var(--white);font-size:14px;font-weight:500}

/* bottom bar */
.bottom-bar{height:64px;background:linear-gradient(90deg,#0a2f6e,#114b9e 50%,#0a2f6e);color:#e6ecf5;font-size:13px}
.bottom-bar .copy{position:absolute;left:100px;top:24px}
.badge{position:absolute;left:876px;top:14px;width:36px;height:36px;border-radius:50%;background:#b69a3e}
.social{position:absolute;left:942px;top:17px;display:flex;gap:14px}
.social i{width:30px;height:30px;border:2px solid var(--white);border-radius:50%}
</style>
</head>
<body>

<header class="site-header">
  <div class="brand"><span class="brand-dot"></span><span class="brand-name">Harbourline</span></div>
  <nav class="main-nav">
    <a class="active" href="#">Home</a>
    <a href="#">About US</a>
    <a href="#">Our Services</a>
    <a href="#">BLog Post</a>
    <a href="#">Contact Us</a>
  </nav>
</header>

<div class="ticker">
  <div class="ticker-label">Forex Ticker</div>
  <div class="ticker-items">
    <span>&gt; British Pound Sterling &nbsp;- 100</span>
    <span>&gt; Hong Kong Dollar &nbsp;- 1078.41</span>
    <span>&gt; Bolivian Boliviano &nbsp;- 2015.20</span>
    <span>Algerian Dinar &nbsp;- 21.2</span>
  </div>
  <svg class="ticker-next" width="20" height="22" viewBox="0 0 20 22"><path d="M3 4l7 7-7 7M10 4l7 7-7 7" fill="none" stroke="#fff" stroke-width="2"/></svg>
</div>

<section class="hero">
  <div class="hero-art" role="img" aria-label="Hand reaching toward glowing digital exchange-rate figures"></div>
  <span class="hero-mark"></span>
  <h1 class="hero-title">Harbourline Incorporation</h1>
  <p class="hero-text">We are a new ForEx &amp; fund remittance entity based in European - Hong Kong.</p>
  <a class="btn btn-outline" href="#">Read More</a>
  <div class="dots"><i></i><i></i><i></i><i></i></div>
</section>

<section class="about">
  <span class="divider" style="top:-30px"></span>
  <h2 class="section-title serif">About <b>Harbourline Incorporation</b></h2>
  <p class="lead">Harbourline is a leading provider of international payment services</p>
  <div class="body">
    <p>Harbourline is a leading provider of international payment services and foreign exchange to corporations and individuals covering most of the world including, throughout Asia, South America, and Europe. We engage with our clients with unmatched personalised service and aim to establish longevity with all our client relationships.</p>
    <p>Coupled with our excellent customer service, highly competitive rates and in depth market knowledge we provide a simple, reliable and cost effective service to all of our clients.</p>
  </div>
  <div class="actions"><a class="btn btn-navy" href="#">Read More</a><a class="btn btn-dark" href="#">Contact Us</a></div>
</section>

<section class="services">
  <span class="divider" style="top:-30px"></span>
  <h2 class="section-title serif">Our Services</h2>
  <p class="lead">Our expertise service areas</p>
  <article class="service-card" style="left:100px">
    <div class="service-photo" role="img" aria-label="Stack of coins on banknotes" style="background:linear-gradient(160deg,#c9b9a4,#8d8a7c 55%,#b7a48a)"></div>
    <h3>International Money Transfer</h3>
  </article>
  <article class="service-card featured" style="left:456px">
    <h3>Foreign Exchange</h3>
    <p>We provide the international settlement and reconciliation of funds for and on behalf of our clients</p>
    <a class="btn" href="#">Read More</a>
  </article>
  <article class="service-card" style="left:812px">
    <div class="service-photo" role="img" aria-label="Business handshake" style="background:linear-gradient(135deg,#f2f2f2,#d8b89a 50%,#3a3a3a)"></div>
    <h3>Paying &amp; Receiving Agency</h3>
  </article>
  <div class="dots"><i></i><i></i><i class="on"></i><i></i><i></i></div>
</section>

<section class="blog">
  <span class="divider" style="top:-30px"></span>
  <h2 class="section-title serif">Harbourline <b>Blog</b></h2>
  <article class="post-card" style="left:100px">
    <div class="post-photo" role="img" aria-label="Group of business people in an office" style="background:linear-gradient(180deg,#eeeeee,#5a5a5e)"></div>
    <h3>Neque porro quisquam dolorem</h3>
    <p>Nemo enim ipsam voluptatem quia voluptas sit aspernatur aut odit aut fugit, sed quia conse quuntur magni dolores eosqui</p>
    <a class="btn btn-navy" href="#">Read More</a>
  </article>
  <article class="post-card" style="left:449px">
    <div class="post-photo" role="img" aria-label="Businesswoman working at a laptop" style="background:linear-gradient(160deg,#f4f4f4,#9aa3ad 60%,#3b3b3b)"></div>
    <h3>Neque porro quisquam dolorem</h3>
    <p>Nemo enim ipsam voluptatem quia voluptas sit aspernatur aut odit aut fugit, sed quia conse quuntur magni dolores eosqui</p>
    <a class="btn btn-dark" href="#">Read More</a>
  </article>
  <article class="post-card" style="left:799px">
    <div class="post-photo" role="img" aria-label="Two colleagues reviewing a document" style="background:linear-gradient(160deg,#e8e2da,#9c7f95 55%,#c34b4b)"></div>
    <h3>Neque porro quisquam dolorem</h3>
    <p>Nemo enim ipsam voluptatem quia voluptas sit aspernatur aut odit aut fugit, sed quia conse quuntur magni dolores eosqui</p>
    <a class="btn btn-dark" href="#">Read More</a>
  </article>
</section>

<footer class="site-footer">
  <span class="divider" style="top:-30px"></span>
  <div class="footer-brand"><span class="brand-dot"></span><span class="brand-name">Harbourline</span></div>
  <ul class="contact-list">
    <li><svg width="12" height="14" viewBox="0 0 12 14"><path d="M6 0a5 5 0 0 0-5 5c0 4 5 9 5 9s5-5 5-9a5 5 0 0 0-5-5zm0 7a2 2 0 1 1 0-4 2 2 0 0 1 0 4z" fill="#fff"/></svg><span>Kestrel House Millbrook Court<br>Millbrook Lane QX4 7LT</span></li>
    <li><svg width="13" height="10" viewBox="0 0 13 10"><rect width="13" height="10" fill="#fff"/><path d="M0 0l6.5 5L13 0" fill="none" stroke="#232323" stroke-width="1.4"/></svg><span>Email: &nbsp;info@harbourline-<br>example.com</span></li>
    <li><svg width="12" height="12" viewBox="0 0 12 12"><rect width="12" height="12" rx="2" fill="#fff"/><path d="M3 2.5l1.6 1.6-.9 1.2a5 5 0 0 0 3 3l1.2-.9L9.5 9 8.5 10C5 9.5 2.5 7 2 3.5z" fill="#232323"/></svg><span>Phone: (852) 5550 1284</span></li>
  </ul>
  <span class="footer-sep" style="left:353px"></span>
  <span class="footer-sep" style="left:634px"></span>
  <span class="footer-sep" style="left:849px"></span>

  <div class="footer-col recent">
    <h3 class="footer-title">Recent Posts</h3>
    <div class="recent-item"><div class="recent-thumb" role="img" aria-label="Blog thumbnail" style="background:linear-gradient(135deg,#c9a27c,#5a6470)"></div><div><h4>Planning For The Future</h4><time>&#128197;&nbsp; NOV 12, 2015</time></div></div>
    <div class="recent-item"><div class="recent-thumb" role="img" aria-label="Blog thumbnail" style="background:linear-gradient(135deg,#d8c8b4,#4e6f8e)"></div><div><h4>Planning For The Future</h4><time>&#128197;&nbsp; NOV 12, 2015</time></div></div>
    <div class="recent-item"><div class="recent-thumb" role="img" aria-label="Blog thumbnail" style="background:linear-gradient(135deg,#7aa59a,#3d4a5a)"></div><div><h4>Planning For The Future</h4><time>&#128197;&nbsp; NOV 12, 2015</time></div></div>
  </div>

  <div class="footer-col links">
    <h3 class="footer-title">Additional Links</h3>
    <ul>
      <li>&gt;&gt; Home</li>
      <li>&gt;&gt; About US</li>
      <li>&gt;&gt; Services</li>
      <li>&gt;&gt; Client Registration</li>
      <li>&gt;&gt; Contact Us</li>
    </ul>
  </div>

  <div class="footer-col contact">
    <h3 class="footer-title">Contact Us</h3>
    <div class="field">Name</div>
    <div class="field">Email Address</div>
    <div class="field area">Comments</div>
    <div class="submit">Contact Us</div>
  </div>
</footer>

<div class="bottom-bar">
  <span class="copy">© 2016 Harbourline Incorporation Limited. All Rights Reserved</span>
  <span class="badge"></span>
  <div class="social"><i></i><i></i><i></i><i></i></div>
</div>

</body>
</html>
```